Yacht, Boats, Watersports company needs a redesign of business card

Hello Designers!
We are a Boat dealership company that sells fun in the water, we sell boats, Yachts, Kayaks and also yacht WaterSport toys. We are looking to redesign our business cards in to something a little bit more sophisticated. in a way that we can make better use of our company colors. I'm attaching a zipped file containing the company 3 sets of company logo which one is an horizontal another one is a vertical and also a chromed 3d logo. Also is included two set of business cards that we use and also some designs that i think it's interesting. We use PMS 2026c Orange and PMS 7687C Blue. I would like to see at least two different options with the orange as accent and also using blue as an accent color. It's really important for the business cards to have a font option and size that is legible to most people. Our current website is wwww.coralpennant.com. Please visit if you want to have a better feeling of the Boat dealership
You can send Single sided or double side options. We are now using single sided but we may be open for a double side option if we really like the design.
Target Market(s)
Marine, boat sales, yacht sales, water toys sales/
Contact Information for Business Card
Name: Dale Whitcombe
Address: 212 North Fenwick Lane,
Gull Harbor, FL 33071
Phone: 954-731-8842
Fax: 954:731-8843
Cell: 954-382-1490
Email: dw@coralpennant.com
Website: coralpennant.com
Requirements
Must have
- the current information of the business card provided.
logo
use the PMS Colors
Nice to have
- a touch of elegance and sophistication but simple
Should not have
- should not have any typography that is hard to read, the card should be simple but yet sophisticated.

```html
<!DOCTYPE html>
<html lang="en">
<head>
<meta charset="utf-8">
<title>Coral Pennant — Business Card</title>
<link href="https://fonts.googleapis.com/css2?family=Open+Sans:wght@400;600;700;800&display=swap" rel="stylesheet">
<style>
  :root {
    --brand-blue: #0059b3;
    --brand-blue-deep: #0a4a8c;
    --brand-orange: #ff6a00;
    --card-white: #f4f4f4;
    --backdrop: #e2e2e2;
    --ink-light: #ffffff;
  }
  * { box-sizing: border-box; margin: 0; padding: 0; }
  html, body { width: 1200px; height: 900px; overflow: hidden; }
  body {
    background: var(--backdrop);
    font-family: "Open Sans", Arial, sans-serif;
    display: flex;
    flex-direction: column;
    align-items: center;
    justify-content: center;
    gap: 36px;
  }
  .card {
    position: relative;
    width: 700px;
    height: 400px;
    overflow: hidden;
    box-shadow: 0 6px 18px rgba(0,0,0,0.18);
  }

  /* Back side: contact details */
  .card-back { background: var(--brand-blue); color: var(--ink-light); }
  .card-back .accent-band { position: absolute; left: 0; bottom: 0; width: 100%; height: 70px; }
  .holder-name {
    position: absolute; left: 150px; top: 70px;
    font-size: 28px; font-weight: 400; letter-spacing: 0.2px;
  }
  .contact-list {
    position: absolute; left: 330px; top: 150px;
    list-style: none; font-size: 15px; line-height: 1.45;
  }
  .contact-list li { display: flex; gap: 10px; align-items: flex-start; margin-bottom: 4px; }
  .contact-list svg { flex: 0 0 14px; width: 14px; height: 14px; margin-top: 4px; }

  /* Front side: brand */
  .card-front { background: var(--card-white); }
  .brand {
    position: absolute; left: 0; right: 0; top: 95px;
    display: flex; flex-direction: column; align-items: center; gap: 26px;
  }
  .brand-dot {
    width: 110px; height: 110px; border-radius: 50%;
    border: 9px solid var(--brand-orange);
  }
  .brand-name {
    font-size: 38px; font-weight: 800; letter-spacing: 3px;
    color: var(--brand-blue-deep); text-transform: uppercase;
  }
  .card-front .footer-band { position: absolute; left: 0; bottom: 0; width: 100%; height: 95px; }
  .website {
    position: absolute; left: 0; right: 0; bottom: 22px;
    display: flex; justify-content: center; align-items: center; gap: 8px;
    color: var(--ink-light); font-size: 20px; font-weight: 400;
  }
  .website svg { width: 17px; height: 17px; }
</style>
</head>
<body>

  <section class="card card-back" aria-label="Business card back">
    <svg class="accent-band" viewBox="0 0 700 70" preserveAspectRatio="none" aria-hidden="true">
      <polygon points="0,25 0,70 700,70 700,25 346,25 340,10 312,10 306,25" fill="var(--brand-orange)"/>
    </svg>
    <h1 class="holder-name">Dale Whitcombe</h1>
    <ul class="contact-list">
      <li>
        <svg viewBox="0 0 14 14" aria-hidden="true"><circle cx="7" cy="7" r="5.5" fill="none" stroke="#fff" stroke-width="1.3"/><circle cx="7" cy="7" r="1.8" fill="#fff"/></svg>
        <span>Address: 212 North Fenwick Lane,<br>Gull Harbor, FL 33071</span>
      </li>
      <li>
        <svg viewBox="0 0 14 14" aria-hidden="true"><path d="M3 1.5 L5.5 1.5 L6.3 4.5 L4.8 5.6 C5.6 7.4 6.6 8.4 8.4 9.2 L9.5 7.7 L12.5 8.5 L12.5 11 C12.5 12 11.6 12.6 10.6 12.4 C6 11.5 2.5 8 1.6 3.4 C1.4 2.4 2 1.5 3 1.5Z" fill="#fff"/></svg>
        <span>954-731-8842<br>Fax: 954:731-8843</span>
      </li>
      <li>
        <svg viewBox="0 0 14 14" aria-hidden="true"><rect x="3.5" y="1" width="7" height="12" rx="1.2" fill="none" stroke="#fff" stroke-width="1.2"/><circle cx="7" cy="11" r="0.8" fill="#fff"/></svg>
        <span>954-382-1490</span>
      </li>
      <li>
        <svg viewBox="0 0 14 14" aria-hidden="true"><circle cx="7" cy="7" r="2.4" fill="none" stroke="#fff" stroke-width="1.3"/><path d="M9.4 5 V8.2 C9.4 9.6 11.8 9.6 12 7.6 C12.4 3.8 9.8 1.5 7 1.5 A5.5 5.5 0 1 0 10.4 11.3" fill="none" stroke="#fff" stroke-width="1.3"/></svg>
        <span>dw@coralpennant.com</span>
      </li>
    </ul>
  </section>

  <section class="card card-front" aria-label="Business card front">
    <div class="brand">
      <div class="brand-dot" aria-hidden="true"></div>
      <p class="brand-name">Coral Pennant</p>
    </div>
    <svg class="footer-band" viewBox="0 0 700 95" preserveAspectRatio="none" aria-hidden="true">
      <polygon points="0,22 318,22 340,0 362,22 700,22 700,95 0,95" fill="var(--brand-blue)"/>
    </svg>
    <p class="website">
      <svg viewBox="0 0 14 14" aria-hidden="true"><circle cx="7" cy="7" r="2.4" fill="none" stroke="#fff" stroke-width="1.3"/><path d="M9.4 5 V8.2 C9.4 9.6 11.8 9.6 12 7.6 C12.4 3.8 9.8 1.5 7 1.5 A5.5 5.5 0 1 0 10.4 11.3" fill="none" stroke="#fff" stroke-width="1.3"/></svg>
      coralpennant.com
    </p>
  </section>

</body>
</html>
```